Website Redesign - We Need Your Magic!

Hello we are looking for you to help us re-design a high end and professional website for a high-end private school.

Here is the current site: http://www.ferndalecrest.com/

NOTE THIS IS DESIGN ONLY, NO CODING :)

The image they want to portray is that of high quality sports and education, in a creative "un-stiff" way.

Menu Bar: Horizontal

Look and Feel:

Site Colors: Dark green and a Gold yellow (logos are attached)

This site will represent a school so the look must be clean, bold, and classy. The site must have a very clean user interface, with things easily recognizable. Think simple.

The site should be visually appealing! If you come to me with templates, or a ton of text you will be out.

This site should be outside the box, we do not want boring, we do not want status quo. This site should instill excitement, innovation, and athletics.

So the main points again are:

1. High-end and classy look, with creative feel
2. Simple and clear navigation style
3. To cover the Junior and High School - Ferndale Crest College Schools

Think outside the box. We look forward to seeing what you come up with!!

Thank you for helping us create an amazing site for the school!

Industry/Entity Type

School

```html
<!DOCTYPE html>
<html lang="en">
<head>
<meta charset="utf-8">
<title>Ferndale Crest College</title>
<link href="https://fonts.googleapis.com/css2?family=Arimo:wght@400;700&family=Open+Sans:wght@600;700&display=swap" rel="stylesheet">
<style>
:root{
  --green:#0c4623;
  --green-dark:#093a1c;
  --gold:#cfc51a;
  --btn-gold:#e3b614;
  --ink:#222;
  --body:#2e2e2e;
  --page:#f3f3f3;
  --footer:#232323;
  --footer-base:#141414;
  --rule:#d9d9d9;
}
*{margin:0;padding:0;box-sizing:border-box}
html,body{width:847px;height:1200px;overflow:hidden;background:var(--page);font-family:"Arimo",Arial,sans-serif;color:var(--body)}
.page{position:relative;width:847px;height:1200px}
.abs{position:absolute}

/* header */
.crest{left:96px;top:30px;width:60px;height:60px;border-radius:50%;background:var(--green);border:4px solid var(--gold)}
.brand{left:198px;top:44px;font-size:26px;font-weight:700;color:var(--green);letter-spacing:.3px}
.tagline{left:199px;top:91px;font-size:12px;font-style:italic;color:var(--ink)}
.contact{left:608px;top:47px;font-size:11.5px;color:var(--ink)}
.contact div{display:flex;align-items:center;gap:10px;height:19px}
.contact .phone{font-weight:700}
.contact a{color:var(--ink)}
.search{left:606px;top:100px;display:flex}
.search input{width:119px;height:25px;border:1px solid #ddd;background:#fff;font:9px "Arimo",sans-serif;padding-left:8px;color:#888}
.search button{width:34px;height:25px;background:#111;color:#fff;border:0;font:13px "Arimo",sans-serif;border-radius:0 3px 3px 0}

/* nav */
.nav{left:0;top:138px;width:847px;height:35px;background:var(--green);display:flex;align-items:center;padding-left:80px}
.nav a{color:#fff;text-decoration:none;font-size:10px;height:35px;display:flex;align-items:center;padding:0 18px;border-right:1px solid #1d5a33}
.nav a:last-child{border-right:0}
.nav a.active{background:var(--gold);color:var(--green-dark);height:23px;padding:0 17px;margin-right:12px;border:0}

/* hero */
.hero{left:0;top:173px;width:847px;height:274px;background:linear-gradient(100deg,#b9c2d0 0%,#8a9bb5 30%,#c9ccd1 55%,#7d8fa8 75%,#d6d3cf 100%)}
.hero-caption{left:104px;top:313px;width:254px;height:61px;background:rgba(20,20,20,.85);text-align:center;font-family:"Open Sans",sans-serif;padding-top:3px}
.hero-caption .l1{font-size:22px;font-weight:600;color:#fff;line-height:28px}
.hero-caption .l2{font-size:15.5px;font-weight:600;color:var(--gold);line-height:24px}

/* main */
h2{font-size:18px;font-weight:700;color:var(--ink)}
.main p{font-size:9.4px;line-height:14px;margin-bottom:14px}
.welcome{left:80px;top:467px;width:460px}
.welcome h2{margin-bottom:14px}
.welcome p{margin-left:1px}
.welcome b{color:var(--green)}
.head{left:78px;top:690px;width:460px}
.head h2{font-size:15.5px;margin-left:2px;margin-bottom:13px}
.portrait{position:absolute;left:2px;top:33px;width:101px;height:88px;background:linear-gradient(135deg,#2f5d40,#c7a48a 60%,#a89b87);border:3px solid #cfcfcf}
.head .side{margin-left:116px;width:344px}
.head .side p{margin-bottom:12px}

/* sidebar */
.signup{left:557px;top:473px;width:210px;height:184px;background:var(--green);border-radius:3px;padding:11px 10px}
.signup h3{font-size:18px;color:#fff;letter-spacing:.6px}
.signup p{font-size:9px;color:#d8e2db;line-height:13px;margin-top:5px}
.signup input{display:block;width:177px;height:24px;border:0;margin-top:13px;padding-left:6px;font:8.5px "Arimo",sans-serif;color:#888;background:#fff}
.signup button{margin-top:8px;width:102px;height:25px;background:var(--btn-gold);border:0;border-radius:3px;font:700 13px "Arimo",sans-serif;letter-spacing:.5px;color:#111}
.side-block{left:555px;width:212px}
.side-block h3{font-size:16px;color:var(--ink);letter-spacing:.6px;padding-bottom:8px}
.bar{height:3px;background:linear-gradient(to right,var(--gold) 32px,var(--green) 32px)}
.side-block ul{list-style:none;margin-top:6px;width:204px}
.side-block li{position:relative;padding-left:16px;border-bottom:1px dotted var(--rule);font-size:9.4px;color:var(--ink)}
.side-block li:last-child{border-bottom:0}
.side-block li::before{content:"";position:absolute;left:4px;top:50%;margin-top:-3px;border-left:4px solid #222;border-top:3px solid transparent;border-bottom:3px solid transparent}
.events li{height:25px;line-height:25px}
.links li{height:25.5px;line-height:25px;font-size:8.5px}

/* footer */
.footer{left:0;top:1050px;width:847px;height:123px;background:var(--footer)}
.sep{top:1066px;width:0;height:100px;border-left:1px dotted #555}
.pin{left:78px;top:1088px}
.addr{left:124px;top:1090px;color:#eee;text-align:right;width:128px}
.addr .n{font-size:12px;font-weight:700;text-align:left;letter-spacing:.2px;white-space:nowrap}
.addr .a{font-size:8.4px;line-height:12px}
.addr a{display:block;margin-top:6px;font-size:8px;color:#ddd}
.follow{left:320px;top:1093px;width:166px;height:52px;background:#2d4d86;display:flex;align-items:center;justify-content:center;color:#fff;font-size:15px;font-weight:700}
.badge{background:#4a4a4a;border-radius:4px}
.copy{left:0;top:1173px;width:847px;height:27px;background:var(--footer-base);color:#ccc;font-size:8.5px;text-align:center;line-height:27px}
</style>
</head>
<body>
<div class="page">

  <div class="abs crest" aria-hidden="true"></div>
  <div class="abs brand">Ferndale Crest College</div>
  <div class="abs tagline">Striving Forward in Learning, Culture, Sport &amp; Life</div>

  <div class="abs contact">
    <div class="phone">
      <svg width="14" height="14" viewBox="0 0 24 24"><path fill="#1d3a24" d="M6.6 10.8a15.2 15.2 0 006.6 6.6l2.2-2.2c.3-.3.7-.4 1-.2 1.1.4 2.3.6 3.6.6.6 0 1 .4 1 1V20c0 .6-.4 1-1 1A17 17 0 013 4c0-.6.4-1 1-1h3.5c.6 0 1 .4 1 1 0 1.3.2 2.5.6 3.6.1.3 0 .7-.2 1z"/></svg>
      <span>0741 203 118 / 0741 556 902</span>
    </div>
    <div>
      <svg width="14" height="11" viewBox="0 0 14 11"><rect x=".5" y=".5" width="13" height="10" fill="none" stroke="#333"/><path d="M.5 .5L7 6l6.5-5.5" fill="none" stroke="#333"/></svg>
      <a href="#">admin@ferndalecrest.com</a>
    </div>
  </div>

  <form class="abs search"><input value="Search...."><button type="button">GO</button></form>

  <nav class="abs nav">
    <a class="active" href="#">HOME</a>
    <a href="#">ABOUT US</a>
    <a href="#">ACADEMICS</a>
    <a href="#">SPORTS</a>
    <a href="#">JOINING FERNDALE CREST</a>
    <a href="#">ABOUT US</a>
    <a href="#">CONTACT US</a>
  </nav>

  <div class="abs hero" role="img" aria-label="Photo of girls playing football, a player about to kick the ball"></div>
  <div class="abs hero-caption">
    <div class="l1">Quality Education</div>
    <div class="l2">A Community Commitment</div>
  </div>

  <section class="abs main welcome">
    <h2>Welcome to Ferndale Crest College</h2>
    <p>Welcome to <b>Ferndale Crest Group of Schools</b> where our School Motto is ‘Unitas’ meaning Togetherness. We aim to work together in every aspect of School life, from academics to sport.</p>
    <p>Ferndale Crest College opened on 9th March 1991 and occupies 95 ha of land amidst the low hills of the Kestrel Range, 10km west of Ashvale. This location encourages focus on School life away from the distractions and hustle and bustle of the larger towns.</p>
    <p>The day scholars have the option of selected bus drop off points for parents to collect day scholars closer to home.</p>
    <p>Ferndale Crest College offers a wide range of academic subjects alongside a varied sport and extra-curricular program.</p>
  </section>

  <section class="abs main head">
    <h2>Headmaster's Message</h2>
    <div class="portrait" role="img" aria-label="Portrait photo of the headmaster"></div>
    <div class="side">
      <p><b>Welcome to Ferndale Crest College.&nbsp; Here at the College we aim to encourage each pupil to be a self-confident, well-rounded individual.</b></p>
      <p>We aim to propel them to the highest level of achievement in both academics and extra-curricular activities to provide them with the life skills they will need when they leave the College and to prepare them to be of value to society.</p>
    </div>
    <p style="margin-top:18px">The College is a warm community which lives out high standards and is rightly proud of its achievements. We are a small enough School for each pupil to be known well, but large enough to offer a wide range of subjects and experience.</p>
    <p>Our Website covers many aspects of the College from how to apply for a place, to the curriculum and to much more.&nbsp; I hope you find it helpful and interesting.</p>
    <p style="margin-top:28px">Please visit and meet the pupils, the staff and see for yourself what Ferndale Crest College can offer your son or daughter.&nbsp; I look forward to welcoming you and your family to Ferndale Crest College.</p>
  </section>

  <aside class="abs signup">
    <h3>Email Sign Up</h3>
    <p>If you would like to be added to the list of parents that receive the School Newsletter,</p>
    <input value="Enter Your name">
    <input value="Enter Your email">
    <button type="button">SUBSCRIBE</button>
  </aside>

  <aside class="abs side-block events" style="top:685px">
    <h3>Upcoming Events</h3>
    <div class="bar"></div>
    <ul>
      <li>Robotic competitions teach students</li>
      <li>Robotic competitions teach students how to</li>
      <li>Robotic competitions teach</li>
      <li>Robotic competitions teach students</li>
      <li>Robotic competitions teach</li>
    </ul>
  </aside>

  <aside class="abs side-block links" style="top:871px">
    <h3>Important Links</h3>
    <div class="bar"></div>
    <ul>
      <li>School Calender</li>
      <li>Registration Form</li>
      <li>Sports Announcements</li>
      <li>2nd Term 2014 Termly Calendar</li>
    </ul>
  </aside>

  <footer class="abs footer"></footer>
  <div class="abs sep" style="left:310px"></div>
  <div class="abs sep" style="left:498px"></div>
  <svg class="abs pin" width="34" height="44" viewBox="0 0 34 44" aria-hidden="true"><path fill="#7a7a7a" d="M17 0C7.6 0 0 7.4 0 16.6 0 28 17 44 17 44s17-16 17-27.4C34 7.4 26.4 0 17 0z"/><circle cx="17" cy="16" r="5.5" fill="#232323"/></svg>
  <div class="abs addr">
    <div class="n">Ferndale Crest College</div>
    <div class="a">12 Harrow Lane,<br>Millbrook 4021</div>
    <a href="#">Click here to see the directions &gt;&gt;</a>
  </div>
  <div class="abs follow">Follow Our Page</div>
  <div class="abs badge" style="left:533px;top:1084px;width:74px;height:26px"></div>
  <div class="abs badge" style="left:624px;top:1082px;width:76px;height:28px"></div>
  <div class="abs badge" style="left:526px;top:1122px;width:88px;height:30px"></div>
  <div class="abs badge" style="left:624px;top:1124px;width:76px;height:28px"></div>
  <div class="abs badge" style="left:716px;top:1082px;width:58px;height:64px;border-radius:6px 6px 28px 28px"></div>

  <div class="abs copy">Copyright © 2015 Ferndale Crest. All Rights Reserved.</div>
</div>
</body>
</html>
```